Diverse, up-scale salon needs eye-catching, unique business cards.

We are looking for a unique business card design for our stylist but that can also be multi functional and used for appointment reminder and referrals. I will need a design in a format that I can modify names and titles going forward. In the past we have had a dark background with the logo on one side, and stylist and contact information on the other but we are open to all ideas. I have included our mission statement as well as branded colors below. The statement doesn't need to go on the card, it's just a reference for target market. We need space for the stylists name, title, instagram handle and then the salons phone number, website and address. I am also open to adding a spot for a qr code linked to the stylist instagram or the salon booking link.

primary brand colors:
#333333 #233415 #36502a #93874a #000000
Mission statement:
Vessolin Hair Studio, a high-end salon located in the lively Downtown Farmington, Michigan, is committed to providing exceptional services in a welcoming and relaxed environment to meet the needs of our diverse clientele.
Our salon specializes in contemporary custom haircuts, coloring, extensions, and barbering and beard grooming services. Our team of skilled stylists is passionate and inventive in their hair styling techniques. At the heart of our salon are values centered on quality, innovation, creativity, and above all, comfort. These core values are evident in every appointment across our customizable array of services.
Our goal is to establish a benchmark for exceptional hair care for every human.
Website: www.vessolinhairstudio.example
instagram: @vessolinhairstudio
address: 41782 Pelham Crest Rd, Farmington MI
phone: 248-613-4087

Industry/Entity Type

Hair Salon

Contact Information for Business Card

Stylist name, title, phone, instagram, website, address, (optional qr code)

Requirements
Should not have
• Does not need mission statement on the card.

```html
<!DOCTYPE html>
<html lang="en">
<head>
<meta charset="utf-8">
<title>Vessolin Hair Studio – Business Card</title>
<link rel="stylesheet" href="https://fonts.googleapis.com/css2?family=Open+Sans:wght@400;700&display=swap">
<style>
  :root {
    --stage: #3a3a3a;
    --stage-dark: #1c1c1c;
    --card: #141414;
    --card-edge: #0a0a0a;
    --gold: #93874a;
    --ink: #f2f2f2;
    --pattern-light: #5a5a5a;
    --pattern-dark: #1e1e1e;
  }
  * { box-sizing: border-box; margin: 0; padding: 0; }
  html, body { width: 1200px; height: 780px; overflow: hidden; }
  body {
    background: linear-gradient(135deg, var(--stage), var(--stage-dark));
    font-family: "Open Sans", sans-serif;
    position: relative;
  }
  .card {
    position: absolute;
    top: 236px;
    width: 540px;
    height: 309px;
    background: var(--card);
    border-radius: 4px;
    box-shadow: 0 18px 40px rgba(0,0,0,.55), 0 0 0 1px var(--card-edge);
    overflow: hidden;
  }
  .card--front { left: 40px; }
  .card--back { left: 620px; }

  /* front */
  .brand-badge {
    position: absolute;
    left: 58px; top: 38px;
    width: 180px; height: 180px;
    border: 3px solid var(--gold);
    border-radius: 50%;
    display: flex; align-items: center; justify-content: center;
    text-align: center;
  }
  .brand-name {
    color: var(--gold);
    font-weight: 700;
    font-size: 17px;
    letter-spacing: 2px;
    line-height: 1.3;
    text-transform: uppercase;
  }
  .address {
    position: absolute;
    left: 30px; top: 246px;
    width: 240px;
    color: var(--ink);
    font-size: 12.5px;
    text-align: center;
  }
  .divider {
    position: absolute;
    left: 282px; top: 60px;
    width: 1.5px; height: 190px;
    background: var(--gold);
    transform: rotate(14deg);
  }
  .stylist {
    position: absolute;
    left: 320px; top: 62px;
  }
  .stylist-name {
    color: var(--gold);
    font-weight: 700;
    font-size: 22px;
    letter-spacing: .5px;
    text-transform: uppercase;
  }
  .stylist-title {
    color: var(--ink);
    font-size: 13.5px;
    margin-top: 2px;
  }
  .contact-list {
    list-style: none;
    margin-top: 18px;
  }
  .contact-list li {
    display: flex; align-items: center;
    gap: 8px;
    color: var(--ink);
    font-size: 13px;
    line-height: 22px;
    white-space: nowrap;
  }
  .contact-icon { width: 11px; height: 11px; flex: none; }

  /* back */
  .pattern-field {
    position: absolute; inset: 0;
    background: linear-gradient(160deg, var(--pattern-light) 0%, var(--pattern-dark) 45%, var(--card) 100%);
    opacity: .55;
  }
  .back-mark {
    position: absolute; inset: 0;
    display: flex; align-items: center; justify-content: center;
  }
  .back-mark .brand-name { font-size: 18px; }
</style>
</head>
<body>

<section class="card card--front" aria-label="Card front">
  <div class="brand-badge">
    <span class="brand-name">Vessolin<br>Hair Studio</span>
  </div>
  <p class="address">41782 Pelham Crest Rd, Farmington MI</p>
  <div class="divider"></div>
  <div class="stylist">
    <h1 class="stylist-name">Marcus Ellery</h1>
    <p class="stylist-title">Managing Director</p>
    <ul class="contact-list">
      <li>
        <svg class="contact-icon" viewBox="0 0 12 12"><path d="M2.5 1 L4.5 1 L5.2 3.6 L4 4.6 Q5 7 7.4 8 L8.4 6.8 L11 7.5 L11 9.5 Q11 11 9.5 11 Q1 10.5 1 2.5 Q1 1 2.5 1Z" fill="var(--gold)"/></svg>
        248-613-4087
      </li>
      <li>
        <svg class="contact-icon" viewBox="0 0 12 12"><rect x="0.5" y="2" width="11" height="8" fill="var(--gold)"/><path d="M0.5 2 L6 6.5 L11.5 2" fill="none" stroke="var(--card)" stroke-width="1"/></svg>
        info@vessolinstudio.example
      </li>
      <li>
        <svg class="contact-icon" viewBox="0 0 12 12"><circle cx="6" cy="6" r="4.5" fill="none" stroke="var(--gold)" stroke-width="1.5"/></svg>
        @vessolinhairstudio
      </li>
      <li>
        <svg class="contact-icon" viewBox="0 0 12 12"><circle cx="6" cy="6" r="5.5" fill="var(--gold)"/><path d="M0.5 6 H11.5 M6 0.5 Q2.5 6 6 11.5 M6 0.5 Q9.5 6 6 11.5" fill="none" stroke="var(--card)" stroke-width=".8"/></svg>
        www.vessolinhairstudio.example
      </li>
    </ul>
  </div>
</section>

<section class="card card--back" aria-label="Card back">
  <div class="pattern-field" role="img" aria-label="Repeating brand-mark pattern in glossy grey and black"></div>
  <div class="back-mark">
    <span class="brand-name">Vessolin Hair Studio</span>
  </div>
</section>

</body>
</html>
```